Simple and Clean business card design

We would like the design to be simple clean and to incorporate our colors.

We are open to your design and talent, we have the dots in our logo as we think of it as data points and we connect data points for people.

We are open to see the great creative and clean design you bring to the table

Contact Information for Business Card

please include: name, position, email, phone and website

Font styles to use
Sans Serif

Requirements
Must have
• my colors incorporated, simplicity
Nice to have
• lots of white space, simplicity
Should not have
• complexicity/ complex art

```html
<!DOCTYPE html>
<html lang="en">
<head>
<meta charset="utf-8">
<title>Nodara Business Card</title>
<link rel="stylesheet" href="https://fonts.googleapis.com/css2?family=Lato:wght@400;700&display=swap">
<style>
  :root {
    --backdrop: #000000;
    --card: #2e2f33;
    --ink: #ffffff;
    --rule: #55575c;
    --brand-blue: #4285f4;
  }
  * { margin: 0; padding: 0; box-sizing: border-box; }
  html, body {
    width: 1200px;
    height: 900px;
    overflow: hidden;
    background: var(--backdrop);
    font-family: "Lato", sans-serif;
    color: var(--ink);
  }
  .card {
    position: absolute;
    width: 458px;
    height: 282px;
    background: var(--card);
    border-radius: 14px;
  }
  .card--front { left: 137px; top: 265px; }
  .card--back { left: 625px; top: 268px; }

  .wordmark {
    position: absolute;
    font-family: "Lato", sans-serif;
    font-weight: 700;
    color: var(--ink);
    line-height: 1;
    white-space: nowrap;
    display: flex;
    align-items: center;
  }
  .card--front .wordmark {
    left: 40px;
    top: 116px;
    font-size: 46px;
  }
  .card--back .wordmark {
    left: 50%;
    top: 50%;
    transform: translate(-50%, -50%);
    font-size: 62px;
  }
  .wordmark__dot {
    display: inline-block;
    border-radius: 50%;
    background: var(--ink);
    margin-right: 10px;
  }
  .card--front .wordmark__dot { width: 12px; height: 12px; }
  .card--back .wordmark__dot { width: 16px; height: 16px; background: var(--brand-blue); margin-right: 12px; }

  .divider {
    position: absolute;
    left: 231px;
    top: 74px;
    width: 1px;
    height: 126px;
    background: var(--rule);
  }
  .identity {
    position: absolute;
    left: 251px;
    top: 80px;
  }
  .identity__name {
    font-size: 20px;
    font-weight: 700;
    line-height: 1.05;
  }
  .identity__role {
    font-size: 13px;
    font-weight: 400;
    line-height: 1.2;
  }
  .contacts {
    position: absolute;
    left: 251px;
    top: 142px;
    list-style: none;
  }
  .contacts__item {
    display: flex;
    align-items: center;
    gap: 3px;
    height: 19.5px;
    font-size: 13.5px;
    font-weight: 400;
  }
  .contacts__icon {
    width: 17px;
    height: 17px;
    flex: none;
  }
</style>
</head>
<body>
  <section class="card card--front">
    <div class="wordmark"><span class="wordmark__dot"></span>Nodara</div>
    <div class="divider"></div>
    <div class="identity">
      <p class="identity__name">Daniel Reyes</p>
      <p class="identity__role">Founder/ CEO</p>
    </div>
    <ul class="contacts">
      <li class="contacts__item">
        <svg class="contacts__icon" viewBox="0 0 20 20" aria-hidden="true">
          <circle cx="10" cy="10" r="8.6" fill="none" stroke="#fff" stroke-width="1.5"/>
          <path d="M6.6 5.6 L8.2 5.4 L9 7.6 L8 8.6 Q9 10.8 11.4 12 L12.4 11 L14.6 11.8 L14.4 13.4 Q13.6 14.4 12.4 14.2 Q7.6 13 5.8 7.6 Q5.6 6.4 6.6 5.6 Z" fill="#fff"/>
        </svg>
        <span>555-014-2287</span>
      </li>
      <li class="contacts__item">
        <svg class="contacts__icon" viewBox="0 0 20 20" aria-hidden="true">
          <circle cx="10" cy="10" r="8.6" fill="none" stroke="#fff" stroke-width="1.5"/>
          <rect x="5" y="6.5" width="10" height="7" rx="0.6" fill="#fff"/>
          <path d="M5 6.8 L10 10.8 L15 6.8" fill="none" stroke="#2e2f33" stroke-width="1"/>
        </svg>
        <span>daniel.reyes@nodara.one</span>
      </li>
      <li class="contacts__item">
        <svg class="contacts__icon" viewBox="0 0 20 20" aria-hidden="true">
          <circle cx="10" cy="10" r="8.6" fill="none" stroke="#fff" stroke-width="1.5"/>
          <circle cx="10" cy="10" r="5" fill="none" stroke="#fff" stroke-width="1"/>
          <ellipse cx="10" cy="10" rx="2.2" ry="5" fill="none" stroke="#fff" stroke-width="1"/>
          <path d="M5 10 H15 M5.8 7.5 H14.2 M5.8 12.5 H14.2" stroke="#fff" stroke-width="0.9"/>
        </svg>
        <span>www.Nodara.one</span>
      </li>
    </ul>
  </section>

  <section class="card card--back">
    <div class="wordmark"><span class="wordmark__dot"></span>Nodara</div>
  </section>
</body>
</html>
```